Upmarket Dessert Lounge needs a Business Card Design

We are an upmarket dessert lounge needing a business card to match our image.

We want something that is simple yet beautiful, feminine, classy, sophisticated and elegant. We want it to stand out and don't mind if it is bold.

The design should include our logo and colours of red or maroon with gold highlights. We don't mind if black is used.

Marlow & Quince

Target Market(s)

For those who like to indulge or treat themselves and give in to their temptations on good quality desserts.

Industry/Entity Type

Business

Requirements
Must have
• Must include our logo and our name

Marlow & Quince

M & Q

```html
<!DOCTYPE html>
<html lang="en">
<head>
<meta charset="utf-8">
<title>Marlow &amp; Quince – Business Card</title>
<link rel="stylesheet" href="https://fonts.googleapis.com/css2?family=Cinzel:wght@400&family=Open+Sans:wght@400;600;700&display=swap">
<style>
  :root {
    --backdrop: #6e4328;
    --card-black: #2a2929;
    --maroon: #7c1416;
    --cream: #f8cf95;
    --cream-text: #f7dcae;
    --band-edge: #3a1a12;
    --white: #ffffff;
  }
  * { box-sizing: border-box; margin: 0; padding: 0; }
  html, body { width: 1200px; height: 402px; overflow: hidden; }
  body {
    background: var(--backdrop);
    font-family: "Open Sans", Arial, sans-serif;
    position: relative;
  }
  .card {
    position: absolute;
    top: 54px;
    width: 512px;
    height: 292px;
    background: var(--card-black);
    box-shadow: 0 3px 8px rgba(0,0,0,.45);
    overflow: hidden;
  }
  .card--front { left: 63px; }
  .card--back { left: 630px; }

  .brand-name {
    position: absolute;
    left: 0; right: 0;
    text-align: center;
    color: var(--cream-text);
    font-family: "Cinzel", Georgia, serif;
    font-weight: 400;
    white-space: nowrap;
  }
  .card--front .brand-name {
    top: 64px;
    font-size: 23px;
    line-height: 34px;
    letter-spacing: 1px;
  }

  .name-band {
    position: absolute;
    left: 0; right: 0;
    top: 180px;
    height: 30px;
    background: var(--cream);
    border-bottom: 3px solid var(--band-edge);
    text-align: center;
    line-height: 28px;
    color: var(--maroon);
  }
  .name-band .person { font-weight: 700; font-size: 15px; }
  .name-band .title { font-size: 12px; }

  .contact-panel {
    position: absolute;
    left: 0; right: 0;
    top: 213px;
    bottom: 0;
    background: var(--maroon);
    color: var(--white);
    font-size: 12.5px;
    text-align: center;
  }
  .contact-row {
    display: flex;
    justify-content: center;
    gap: 20px;
    margin-top: 11px;
  }
  .contact-item { display: inline-flex; align-items: center; gap: 3px; }
  .contact-item svg { width: 11px; height: 11px; fill: none; stroke: var(--white); stroke-width: 1.6; }
  .contact-line { margin-top: 3px; }
  .contact-line--address { margin-top: 9px; }

  .card--back .brand-name {
    top: 82px;
    font-size: 80px;
    line-height: 110px;
    letter-spacing: 2px;
  }
</style>
</head>
<body>
  <section class="card card--front" aria-label="Business card front">
    <div class="brand-name">Marlow &amp; Quince</div>

    <div class="name-band">
      <span class="person">Your name,</span> <span class="title">Title</span>
    </div>

    <div class="contact-panel">
      <div class="contact-row">
        <span class="contact-item">
          <svg viewBox="0 0 12 12"><path d="M3 1.5l1.5 2.5-1 1c.6 1.3 1.6 2.3 2.9 2.9l1-1 2.5 1.5-.7 2C6 10.2 1.8 6 1.1 2.2z"/></svg>987-654-3210
        </span>
        <span class="contact-item">
          <svg viewBox="0 0 12 12"><rect x="3" y="1" width="6" height="10" rx="1"/><line x1="5" y1="9" x2="7" y2="9"/></svg>987-654-3210
        </span>
        <span class="contact-item">
          <svg viewBox="0 0 12 12"><circle cx="6" cy="6" r="4.8"/><ellipse cx="6" cy="6" rx="2" ry="4.8"/><line x1="1.2" y1="6" x2="10.8" y2="6"/></svg>www.marlow&amp;quince.com
        </span>
      </div>
      <div class="contact-line">info@marlow&amp;quince.com</div>
      <div class="contact-line contact-line--address">Street Name, City Name, State Zip Code</div>
    </div>
  </section>

  <section class="card card--back" aria-label="Business card back">
    <div class="brand-name">M &amp; Q</div>
  </section>
</body>
</html>
```